Church Website with Home Page and Member Sermon Library

I am in need of an updated design for our church website. This will include 4 pages (outlined below). We are a conservative, evangelical, Christian church. The site should be modern and clean, while still reflecting our conservative values. I already have a logo for our church, and I want the site to incorporate the logo, and match the logo/branding. Stock photos are allowed if needed, but I have uploaded some images of our church and would prefer those images to be used if possible. Any stock photos used should not include any people in the photos (scenery, nature, buildings, animals, etc. are fine).

The site will need 4 pages: Home, Support Us (Donate), Login, and Recording Library.

Page 1: Home
The home page should include the following sections:

- Navigation: Should include links to each section of the home page plus a "listen live" link which will take the user to a live-streaming site and a "support us" link which will take the user to a support/donate page.

- Announcements: Can be either a banner or some other design, but there needs to be some way for us to post announcements for visitors to see. I'm open for creative ideas in this section, but would like it not to take up a lot of room on the page.

- About Us: Should include address, service times (see attached document), and information about the church.

- Pastor Bio: A section that introduces our pastor and gives a short bio about our pastor. Would like this section to include a picture of our pastor. Somewhere in this section I would like to include this Bible reference: "And I will give you pastors according to mine heart, which shall feed you with knowledge and understanding. Jer 3:15 LPW"

- Articles of Faith (What We Believe): This should include several sub-sections each with a heading, body, and possibly 1 or more scripture references. I have attached a document to the brief that includes our articles of faith. Feel free to be creative with this section in how you lay these out and format them.

- Support Us: A small section that explains what kind of support someone can give and a link to a donation page. The link can say something like "Support Us" or "Donate Now".

- Contact form: A contact form that allows the visitor to send us a message. The contact form should ask for name, email, phone, and message.

- Footer: A footer that will be displayed on all pages of the site. This should include at a minimum a link to the home page (or a link to each individual section in the home page if you prefer), a link to "listen live", a link to "support us", a link to "contact us" (or you can put the contact form directly in the footer if you prefer), the address, and a "member login" link.

Page 2: Support Us
The donation page should include a form the visitor can fill out to make a donation. We will embed a third party form later. For this design, please just mock out the design with a basic form asking for name, phone, and email.

Page 3: Login
The recording library (detailed below) will require members to login with a shared numeric code before accessing the page. We need a design for a login screen. The screen should include navigation/footer just like all other pages, but the body of the login page will consist only of a form that asks the user to enter the access code and then a "login" button.

Page 4: Recording Library

The library page is a member-only page that will require a shared, numeric pass code to access. On this page, members will be able to access a filterable list of past sermons. The page by default should display most recent sermons, but should also include a search form that allows the member to filter the sermon list to find a particular sermon. The search form should allow the user to select a filter type (e.g. Speaker name, date, event, etc.) and type in a value to search. They should be able to add multiple filters and remove filters that have been added. Each sermon that is displayed in the result list should include basic information such as title, date, speaker, tags, etc. along with a download icon, and an embedded audio player where they can click a play button to stream it on-demand. Each sermon should also have clickable tags associated with it that can be used to find related sermons.
Updates

I have uploaded several images of our church. Feel free to incorporate these into your design if possible.

Target Market(s)

Church Members

Industry/Entity Type

Religion

Number of Pages Required

4 page

Font styles to use
Sans Serif

Colors

Designer to choose colors to be used in the design.

Requirements
Must have
• Must incorporate the logo (attached)
Nice to have
• Would like the design to incorporate pictures of our church (attached) instead of stock photos if possible.
Should not have
• Please avoid an overly cluttered design. Stock photos used should not include any people in the photos.

```html
<!DOCTYPE html>
<html lang="en">
<head>
<meta charset="utf-8">
<title>Cornerstone Hope Church</title>
<link rel="stylesheet" href="https://fonts.googleapis.com/css2?family=Cinzel:wght@400;700&family=Josefin+Sans:wght@400&family=Montserrat:wght@400;500;600&family=Arimo:ital,wght@0,400;0,700;1,400;1,700&display=swap">
<style>
:root{
  --green:#7ea862;
  --green-dark:#4b6d27;
  --green-head:#3e6120;
  --green-soft:#9dc189;
  --blue:#00b9d8;
  --grey-bg:#ececec;
  --text:#555;
  --white:#fff;
}
*{margin:0;padding:0;box-sizing:border-box}
html,body{width:1200px;height:4498px;overflow:hidden}
body{position:relative;background:var(--white);font-family:"Arimo",Arial,sans-serif;color:var(--text)}
.abs{position:absolute}
/* header */
.site-header{left:0;top:0;width:1200px;height:84px;background:var(--white)}
.brand{display:flex;align-items:center;gap:10px;font-family:"Cinzel",serif;font-weight:400;color:var(--green);letter-spacing:1px}
.brand-mark{width:16px;height:16px;background:var(--blue)}
.header-brand{left:131px;top:27px;font-size:22px}
.main-nav{left:372px;top:36px;display:flex;font-family:"Montserrat",sans-serif;font-size:12px;color:#5a5a5a}
.main-nav span{margin-right:22px}
.main-nav .sep{color:var(--green);margin-right:22px}
.pill{border-radius:20px;color:var(--white);font-family:"Montserrat",sans-serif;font-size:12px;display:flex;align-items:center;justify-content:center;letter-spacing:.3px}
.btn-live{left:854px;top:26px;width:121px;height:35px;background:var(--green)}
.btn-support{left:980px;top:26px;width:122px;height:35px;background:var(--blue)}
/* hero */
.hero{left:0;top:84px;width:1200px;height:618px;background:linear-gradient(180deg,#d8d8d6 0%,#d2d1cd 30%,#a5795f 52%,#8a6650 68%,#6e675f 82%,#8c8a86 100%)}
.welcome-tag{left:520px;top:143px;width:165px;height:30px;background:var(--green);color:var(--white);font-family:"Montserrat",sans-serif;font-size:17px;letter-spacing:2px;display:flex;align-items:center;justify-content:center}
.hero-title{left:0;top:180px;width:1200px;text-align:center;font-family:"Cinzel",serif;font-weight:400;font-size:62px;line-height:62px;color:var(--green)}
.hero-title .line2{color:var(--green-dark)}
/* announcement */
.announce{left:0;top:702px;width:1200px;height:112px;background:var(--green)}
.announce-label{left:0;top:702px;width:475px;height:112px;background:var(--green-dark);color:var(--white);font-family:"Cinzel",serif;font-size:33px;display:flex;align-items:center;justify-content:center;letter-spacing:1px}
.announce-text{left:524px;top:737px;color:var(--white);font-family:"Montserrat",sans-serif}
.announce-text b{display:block;font-size:15px;font-weight:600;margin-bottom:8px}
.announce-text span{font-size:15px}
/* about */
.about-frame{left:79px;top:913px;width:230px;height:301px;border:2px solid #9a9a9a}
.about-photo{left:89px;top:924px;width:486px;height:377px;background:linear-gradient(180deg,#e2e2e0 0%,#d6d6d4 35%,#a98470 52%,#8e6d5c 62%,#a9a6a0 78%,#c4c2bc 100%)}
.blue-line{background:var(--blue)}
.section-title{font-family:"Cinzel",serif;font-weight:700;color:var(--green-head)}
.about-title{left:644px;top:922px;font-size:37px}
.about-copy{left:646px;top:1001px;width:430px;font-size:14.5px;line-height:27px}
.about-copy p{margin-bottom:6px}
.timing-label{left:648px;top:1204px;font-family:"Montserrat",sans-serif;font-size:16px;color:var(--green);font-weight:500}
.timing{font-size:12px;font-weight:700;color:#333}
/* pastor */
.pastor-bg{left:0;top:1425px;width:1200px;height:558px;background:linear-gradient(180deg,#f1f1f1 0%,#e6e6e6 45%,#dedede 65%,#ececec 100%)}
.title-center{left:0;width:1200px;text-align:center;font-size:40px}
.underline{height:3px;background:var(--green)}
.pastor-copy{left:126px;top:1610px;width:470px;font-size:15px;line-height:23px}
.pastor-copy p{margin-bottom:8px}
.quote-box{left:122px;top:1794px;width:465px;height:105px;background:var(--green);border-radius:26px 0 26px 0;color:var(--white);padding:22px 26px 0 44px;font-size:13.5px;line-height:20px}
.quote-box i{font-weight:700;display:block}
.quote-box span{display:block;margin-top:10px;font-size:14px}
.pastor-frame{left:648px;top:1598px;width:416px;height:421px;border:2px solid var(--green)}
.pastor-accent{left:929px;top:1886px;width:135px;height:133px;background:var(--blue)}
.pastor-photo{left:662px;top:1612px;width:391px;height:398px;background:linear-gradient(160deg,#7a6a5c 0%,#3f3a36 40%,#1e1d1d 70%,#2b2a2a 100%)}
/* articles */
.card{border:1.5px solid #c9ddbb;background:var(--white);padding:42px 22px 0 36px}
.card::before{content:"";position:absolute;left:-1px;top:44px;width:3px;height:30px;background:var(--green-dark)}
.card h3{font-family:"Josefin Sans",sans-serif;font-weight:400;font-size:22px;letter-spacing:3px;color:var(--green-head);margin-bottom:10px}
.card p{font-size:13.5px;line-height:25px;color:#555}
.card .small{font-size:12.5px;line-height:26px}
/* support */
.support{left:0;top:3133px;width:1200px;height:404px;background:var(--blue)}
.support-title{left:157px;top:3210px;font-family:"Cinzel",serif;font-size:40px;color:var(--white)}
.support-copy{left:161px;top:3297px;width:420px;color:var(--white);font-size:15px;line-height:28.5px}
.checks{left:636px;top:3292px;color:var(--white);font-family:"Montserrat",sans-serif;font-size:17px;font-weight:500}
.checks li{list-style:none;display:flex;align-items:center;gap:9px;height:35px}
.btn-donate{left:632px;top:3413px;width:182px;height:44px;border:2px solid var(--white);border-radius:24px;color:var(--white);font-family:"Montserrat",sans-serif;font-size:13px;font-weight:600;display:flex;align-items:center;justify-content:center}
/* contact */
.contact{left:0;top:3537px;width:1200px;height:582px;background:linear-gradient(180deg,#9cc187 0%,#94bb80 45%,#88b277 70%,#93ba80 100%)}
.contact-title{left:0;top:3630px;width:1200px;text-align:center;font-family:"Cinzel",serif;font-size:40px;color:var(--white)}
.field{background:var(--white);border:1px solid #d5d5d5;font-family:"Montserrat",sans-serif;font-size:13px;color:#666;padding:0 19px;display:flex;align-items:center}
.field.msg{align-items:flex-start;padding-top:14px}
.btn-send{left:529px;top:3981px;width:194px;height:45px;background:var(--blue);border-radius:24px;color:var(--white);font-family:"Montserrat",sans-serif;font-size:14px;font-weight:500;display:flex;align-items:center;justify-content:center}
/* footer */
.footer-divider{top:4119px;width:1px;height:290px;background:#ddd}
.footer-brand{left:122px;top:4207px;font-size:20px}
.foot-head{font-family:"Montserrat",sans-serif;font-size:14px;letter-spacing:2px;color:var(--green-dark);font-weight:500}
.foot-links{left:410px;top:4228px;font-family:"Montserrat",sans-serif;font-size:13px;color:#555;line-height:30px;list-style:none}
.foot-text{font-size:12.5px;line-height:19px;color:#555}
.btn-foot-donate{left:603px;top:4307px;width:132px;height:30px;background:var(--green);font-size:10px}
.btn-member{left:861px;top:4300px;width:134px;height:30px;background:var(--blue);font-size:10px}
.copyright{left:0;top:4440px;width:1200px;height:58px;background:#f0f0ee;font-size:12px;color:#777;display:flex;align-items:center;justify-content:center}
</style>
</head>
<body>

<!-- Header -->
<header class="abs site-header">
  <div class="abs brand header-brand"><span class="brand-mark"></span>Cornerstone Hope</div>
  <nav class="abs main-nav">
    <span>ABOUT US</span><span class="sep">|</span>
    <span>PASTOR BIO</span><span class="sep">|</span>
    <span>ARTICLES OF FAITH</span><span class="sep">|</span>
    <span>CONTACT</span>
  </nav>
  <div class="abs pill btn-live">LISTEN LIVE</div>
  <div class="abs pill btn-support">SUPPORT US</div>
</header>

<!-- Hero -->
<section class="abs hero" role="img" aria-label="Photo of the brick church building under an overcast sky"></section>
<div class="abs welcome-tag">WELCOME TO</div>
<h1 class="abs hero-title">CORNERSTONE HOPE<br><span class="line2">CHURCH</span></h1>

<!-- Announcement -->
<div class="abs announce"></div>
<div class="abs announce-label">ANNOUNCEMENT</div>
<div class="abs announce-text">
  <b>LOREM IPSUM DOLOR SIT AMET CONSECTETUR ADIPISCING</b>
  <span>Ut enim ad minim veniam quis nostrud exercitatio</span>
</div>

<!-- About -->
<div class="abs about-frame"></div>
<div class="abs about-photo" role="img" aria-label="Photo of the church building side view with parking lot"></div>
<div class="abs blue-line" style="left:581px;top:1013px;width:7px;height:300px"></div>
<div class="abs blue-line" style="left:358px;top:1306px;width:230px;height:7px"></div>
<h2 class="abs section-title about-title">ABOUT OUR CHURCH</h2>
<div class="abs about-copy">
  <p>Lorem ipsum dolor sit amet, consectetur adipiscing elit, sed do eiusmod tempor incididunt ut labore et dolore magna aliqua. Ut enim ad minim veniam, quis nostrud exercitation</p>
  <p>Allamco laboris nisi ut aliquip ex ea commodo consequat. Duis aute irure dolor in reprehenderit in voluptate velit esse cillum dolore eu fugiat nulla pariatur.</p>
</div>
<div class="abs timing-label">SERVICE TIMING:</div>
<div class="abs timing" style="left:650px;top:1243px">Wednesday Night Service: 7:30 PM</div>
<div class="abs timing" style="left:885px;top:1244px">Sunday Morning Service: 11:00 AM</div>
<div class="abs timing" style="left:650px;top:1273px">Sunday School: 10:00 AM</div>
<div class="abs timing" style="left:885px;top:1274px">Sunday Night Service: 5:30 PM</div>

<!-- Pastor -->
<section class="abs pastor-bg" role="img" aria-label="Faded photo of the church building in the background"></section>
<h2 class="abs section-title title-center" style="top:1484px">OUR PASTOR</h2>
<div class="abs underline" style="left:550px;top:1543px;width:96px"></div>
<div class="abs pastor-copy">
  <p>Lorem ipsum dolor sit amet, consectetur adipiscing elit, sed do eiusmod tempor incididunt ut labore et dolore magna aliqua. Ut enim ad minim veniam, quis nostrud exercitation</p>
  <p>Allamco laboris nisi ut aliquip ex ea commodo consequat. Duis aute irure dolor in reprehenderit in voluptate velit esse ea commodo consequat. Duis aute irure dolor in</p>
</div>
<div class="abs quote-box">
  <i>“And I will give you pastors according to mine heart, which shall feed you with knowledge and understanding”</i>
  <span>Jer 3:15 LPW</span>
</div>
<div class="abs pastor-frame"></div>
<div class="abs pastor-accent"></div>
<div class="abs pastor-photo" role="img" aria-label="Portrait of the pastor holding an open Bible"></div>

<!-- Articles of Faith -->
<h2 class="abs section-title title-center" style="top:2103px">ARTICLES OF FAITH</h2>
<div class="abs underline" style="left:560px;top:2159px;width:90px"></div>

<article class="abs card" style="left:141px;top:2213px;width:467px;height:260px">
  <h3>THE GOD HEAD.</h3>
  <p>We believe in the God head bodily, known as the Divine Trinity. This body consist of God the father, Jesus Christ, his only begotten son and the redeemer of the world, and of the Holy Ghost, The third person of the Divine Trinity.</p>
</article>
<article class="abs card" style="left:620px;top:2213px;width:466px;height:260px">
  <h3>BAPTISM OF THE HOLY GHOST</h3>
  <p>We believe in the baptism of the Holy Ghost as it is taught in the Bible and promised by our Lord Jesus Christ, with speaking in tongues as the Spirit gives utterance as the initial evidence. Acts 2:4 we believe that the gift of the Holy Ghost is for all believers as the Lord promised. Acts 2:17-1</p>
</article>
<article class="abs card" style="left:141px;top:2489px;width:467px;height:393px">
  <h3>FULL SALVATION</h3>
  <p class="small">We believe that Salvation is received only when a person comes to the realization that he or she is lost and separated from God and becomes full of godly sorrow, confessing their sins and true repentance, believing in the shed blood of the Lord Jesus Christ as the only sacrifice for sins. Through the blood of Christ we have:</p>
  <p class="small" style="margin-top:14px;line-height:27px">(1) remission of sins, Matthew 26:28 Heb 9:22<br>(2) Sanctification. Hebrews 13:12<br>(3) redemption. Revelations 5:9<br>(4) cleansing. 1 John 1:7 Rev. 1:5<br>(5). Justification. Romans 5:9</p>
</article>
<article class="abs card" style="left:620px;top:2489px;width:466px;height:156px;padding-top:32px">
  <h3>DIVINE HEALING</h3>
  <p class="small">We believe Divine Healing to be included in the atonement of Jesus Christ our Lord, And believe that it is still for us today. 1 Peter 2:24 Luke 9:1-2 Mark 16-18 James 5:15</p>
</article>
<article class="abs card" style="left:620px;top:2662px;width:466px;height:157px;padding-top:32px">
  <h3>SECOND COMING OF CHRIST</h3>
  <p>We believe in the second coming of Jesus Christ. Matthew 24:44 Luke 12:40</p>
</article>
<article class="abs card" style="left:141px;top:2898px;width:467px;height:159px;padding-top:30px">
  <h3>ETERNITY</h3>
  <p>We believe in Literal Eternity. Eternal Life for the believer and eternal death for those without Christ. Revelations 21:1-27</p>
</article>
<article class="abs card" style="left:620px;top:2840px;width:466px;height:217px;padding-top:32px">
  <h3>SANCTIFICATION</h3>
  <p>“Sanctify them through thy truth thy word is truth St John 17:17. For this is the will of God even your sanctification”</p>
  <p style="margin-top:6px">We believe in a set apart life, separate from the world to Christ 2 Cor 6:17-18</p>
</article>

<!-- Support -->
<section class="abs support"></section>
<h2 class="abs support-title">SUPPORT US</h2>
<p class="abs support-copy">Lorem ipsum dolor sit amet, consectetur adipiscing elit, sed do eiusmod tempor incididunt ut labore et dolore magna aliqua. Ut enim ad minim Lorem ipsum dolor sit amet, consectetur adipiscinnim ad minim Lorem ipsum dolor sit ipsum dolor sit amet, consectetur</p>
<ul class="abs checks">
  <li><svg width="20" height="16" viewBox="0 0 20 16"><path d="M2 8l5 5L18 2" fill="none" stroke="#fff" stroke-width="3"/></svg>Consectetur adipiscing elit, sed do</li>
  <li><svg width="20" height="16" viewBox="0 0 20 16"><path d="M2 8l5 5L18 2" fill="none" stroke="#fff" stroke-width="3"/></svg>Eiusmod tempor incididunt ut labore et dolore</li>
  <li><svg width="20" height="16" viewBox="0 0 20 16"><path d="M2 8l5 5L18 2" fill="none" stroke="#fff" stroke-width="3"/></svg>Magna aliqua Ut enim ad minim</li>
</ul>
<div class="abs btn-donate">DONATE NOW</div>

<!-- Contact -->
<section class="abs contact" role="img" aria-label="Green-tinted photo of the church building"></section>
<h2 class="abs contact-title">CONTACT US</h2>
<div class="abs underline" style="left:556px;top:3690px;width:90px;background:#fff"></div>
<div class="abs field" style="left:229px;top:3727px;width:391px;height:53px">First Name</div>
<div class="abs field" style="left:629px;top:3727px;width:391px;height:53px">Last Name</div>
<div class="abs field" style="left:229px;top:3794px;width:391px;height:52px">Email address</div>
<div class="abs field" style="left:629px;top:3794px;width:391px;height:52px">Phone</div>
<div class="abs field msg" style="left:229px;top:3858px;width:791px;height:100px">Message</div>
<div class="abs btn-send">SEND MESSAGE</div>

<!-- Footer -->
<footer>
  <div class="abs brand footer-brand"><span class="brand-mark"></span>Cornerstone Hope</div>
  <div class="abs footer-divider" style="left:383px"></div>
  <div class="abs footer-divider" style="left:583px"></div>
  <div class="abs footer-divider" style="left:838px"></div>
  <div class="abs blue-line" style="left:383px;top:4190px;width:2px;height:22px"></div>
  <div class="abs blue-line" style="left:583px;top:4190px;width:2px;height:22px"></div>
  <div class="abs blue-line" style="left:838px;top:4190px;width:2px;height:22px"></div>

  <div class="abs foot-head" style="left:407px;top:4191px">NAVIGATION</div>
  <ul class="abs foot-links">
    <li>About Us</li><li>Paster Bio</li><li>Article of Faith</li><li>Listen Live</li><li>Contact Us</li>
  </ul>

  <div class="abs foot-head" style="left:604px;top:4191px">DONATION</div>
  <p class="abs foot-text" style="left:606px;top:4230px;width:215px">Lorem ipsum dolor sit amet, consectetur adipiscing elit, sed do eiusmod tempor inci</p>
  <div class="abs pill btn-foot-donate">DONATE NOW</div>

  <div class="abs foot-head" style="left:866px;top:4193px">CONTACT US</div>
  <svg class="abs" style="left:866px;top:4229px" width="32" height="32" viewBox="0 0 32 32">
    <circle cx="16" cy="16" r="16" fill="#7ea862"/>
    <path d="M16 7a6 6 0 0 0-6 6c0 4.5 6 11 6 11s6-6.5 6-11a6 6 0 0 0-6-6z" fill="#fff"/>
    <circle cx="16" cy="13" r="2.3" fill="#7ea862"/>
  </svg>
  <p class="abs foot-text" style="left:908px;top:4228px;width:150px;font-size:11.5px;line-height:16px;color:#333">88 Elm Row, Suite 210, Fairview, NY 10990 USA</p>
  <div class="abs pill btn-member">MEMBER LOGIN</div>

  <div class="abs copyright">© 2023 Cornerstone Hope Church. All Rights Reserved</div>
</footer>

</body>
</html>
```